Web-site design for company trading in chemicals & lubricants

We need a standard 5 page web-site designed for our company based in Dubai, UAE.
The web-site should highlight our capacity to store material as well as distribute the same. The products we sell are basic chemicals - packed in bags as well as drums. Bags are big bags - 25 kgs each as well as drums - 200 litres each. We want to highlight the fact that we huge stocks of this material & can deliver by sea & road,
Please use this site as a ref - http://www.brontex-solvents.co.uk/
Besides this, we need a page dedicated to finished products that we are selling for use in the auto industry - lubricants, motor oils,brake-fluids, greases, coolants etc. This are packed in large drums as well as small cans.
It would be nice if the site could immediately also provide a ref. to our location - Dubai or that we are based in the Middle East.
We will provide our company logo for reference

```html
<!DOCTYPE html>
<html lang="en">
<head>
<meta charset="utf-8">
<title>Korvane – Chemicals &amp; Lubricants</title>
<link href="https://fonts.googleapis.com/css2?family=Arimo:wght@400;700&display=swap" rel="stylesheet">
<style>
:root{
  --brown:#4a2a14;
  --olive:#7a6a1a;
  --gold:#c9a227;
  --dark:#2a2a2a;
  --text:#333;
  --rule:#d8d8d8;
  --panel:#e4e4e4;
  --footer:#333;
}
*{margin:0;padding:0;box-sizing:border-box}
html,body{width:863px;height:1200px;overflow:hidden;background:#fff}
body{position:relative;font-family:"Arimo",Arial,sans-serif;color:var(--text);font-size:11px}
.abs{position:absolute}
/* header */
.brand{left:16px;top:40px;display:flex;align-items:center;gap:10px;font-size:40px;font-weight:700;color:var(--brown);letter-spacing:2px}
.brand-dot{width:26px;height:26px;border-radius:50%;background:var(--olive)}
.connect{left:780px;top:12px;font-size:11px;color:#333}
.social{top:27px;width:26px;height:26px;border-radius:4px}
.nav{top:67px;left:436px;display:flex;align-items:center;gap:12px;font-size:11px;font-weight:700;color:var(--brown)}
.header-rule{left:18px;top:100px;width:827px;height:1px;background:var(--rule)}
/* hero */
.hero{left:18px;top:102px;width:827px;height:378px;background:#fff;border:1px solid var(--rule);box-shadow:0 2px 4px rgba(0,0,0,.12)}
.hero-photo{left:31px;top:123px;width:800px;height:305px;border-radius:6px 6px 0 0;background:linear-gradient(180deg,#6e7a4c 0%,#7c845a 35%,#8c9098 60%,#6f7880 100%)}
.hero-title{left:53px;top:148px;font-size:17px;font-weight:700;color:#fff}
.hero-lead{left:53px;top:177px;width:440px;font-size:12.5px;line-height:16px;color:#fff}
.hero-menu{left:68px;top:262px;width:154px;height:166px;background:rgba(20,20,20,.82);padding:20px 0 0 38px;list-style:none}
.hero-menu li{height:26px;font-size:11px;color:#eee;position:relative}
.hero-menu li::before{content:"";position:absolute;left:-17px;top:3px;width:6px;height:6px;border-radius:50%;background:var(--gold)}
.hero-menu li.active{color:var(--gold)}
.pointer{left:128px;top:420px;width:0;height:0;border-left:8px solid transparent;border-right:8px solid transparent;border-bottom:8px solid #fff}
.tab{top:443px;font-size:17px;font-weight:700;text-align:center}
.tab-sep{top:436px;width:1px;height:38px;background:#ccc}
/* content */
.h2{font-size:13px;font-weight:700;color:var(--brown)}
.arrows{display:inline-block;margin-left:6px;color:#555;font-size:12px;letter-spacing:-1px}
.intro{left:26px;top:542px;width:550px;line-height:15.5px}
.deal-img{top:645px;width:150px;height:80px}
.deal-title{top:731px;font-weight:700;color:#222}
.deal-text{top:756px;width:175px;line-height:16px}
.readmore{top:802px;width:64px;height:19px;border:1px solid #bbb;border-radius:10px;font-size:9px;padding:4px 0 0 6px;background:#fafafa}
.readmore::after{content:"";position:absolute;right:3px;top:3px;width:11px;height:11px;border-radius:50%;background:#222}
.avatar{left:24px;width:42px;height:44px;background:#555;border:2px solid #ccc}
.quote-name{left:82px;font-weight:700;color:#222}
.quote-text{left:82px;width:280px;line-height:15.5px}
.link{color:var(--brown);font-size:11px}
.news-title{left:398px;font-weight:700;color:#222}
.news-text{left:398px;width:190px;line-height:16px}
/* sidebar */
.sidebar{left:608px;top:499px;width:235px;height:612px;background:var(--panel);border:1px solid #ccc;border-radius:4px}
.field{height:20px;background:#ccc;color:#444;padding:3px 0 0 16px;font-size:11px}
.btn{height:20px;background:var(--olive);color:#fff;text-align:center;padding-top:3px;font-size:11px;border:1px solid #5e5214}
.az-box{left:616px;top:591px;width:220px;height:194px;background:var(--dark);padding:14px 0 0 12px;color:#eee}
.az-box p{height:44px;line-height:15px}
.az-box b{color:#fff}
.az-tab{left:782px;top:571px;width:54px;height:20px;background:var(--dark)}
.sectors{left:627px;top:830px;list-style:none;width:200px}
.sectors li{position:relative;padding-left:16px;line-height:14px;margin-bottom:9px}
.sectors li::before{content:"";position:absolute;left:2px;top:4px;width:7px;height:7px;border-radius:50%;background:#222}
.map{left:623px;top:953px;width:210px;height:139px;background:linear-gradient(135deg,#a9c7e8 0%,#d7dfc8 45%,#ece6cf 70%,#e3dcc4 100%)}
/* footer */
.footer{left:0;top:1120px;width:863px;height:80px;background:var(--footer);border-top:2px solid #555}
.foot-links{left:272px;top:1138px;color:#ddd;font-size:11px}
.copy{left:353px;top:1164px;color:#ccc;font-size:11px}
.newsletter{left:631px;top:1131px;color:#fff;font-size:13px}
</style>
</head>
<body>

<header>
  <div class="abs brand"><span>KORVANE</span><span class="brand-dot"></span></div>
  <div class="abs connect">Connect Us</div>
  <span class="abs social" style="left:744px;background:#2f6fb5" aria-hidden="true"></span>
  <span class="abs social" style="left:778px;background:#3b9ad9" aria-hidden="true"></span>
  <span class="abs social" style="left:812px;background:#e8891c" aria-hidden="true"></span>
  <nav class="abs nav">
    <svg width="22" height="18" viewBox="0 0 22 18" aria-label="Home"><path d="M11 1 L1 9 H4 V17 H9 V12 H13 V17 H18 V9 H21 Z" fill="#222"/></svg>
    <span style="margin-left:8px">ABOUT</span><span>PARTNERS</span><span>BUSINESS FIELDS</span><span>PRODUCTS</span><span>CONTACT US</span>
  </nav>
  <div class="abs header-rule"></div>
</header>

<section>
  <div class="abs hero"></div>
  <div class="abs hero-photo" role="img" aria-label="Aerial photo of an industrial storage site with silos and tanker trucks"></div>
  <div class="abs hero-title">Industrial</div>
  <div class="abs hero-lead">It is a long established fact that a reader will be distracted by the readable content of a page when looking at its layout</div>
  <ul class="abs hero-menu">
    <li class="active">Overview</li><li>Markets</li><li>Functionalities</li><li>Products</li><li>Partners</li>
  </ul>
  <div class="abs pointer"></div>
  <div class="abs tab" style="left:31px;width:214px;color:#2b2b2b">Industrial</div>
  <div class="abs tab-sep" style="left:282px"></div>
  <div class="abs tab" style="left:300px;width:250px;color:var(--olive)">Pharmaceutical</div>
  <div class="abs tab-sep" style="left:584px"></div>
  <div class="abs tab" style="left:600px;width:238px;color:var(--olive)">Personal Care</div>
</section>

<main>
  <h1 class="abs h2" style="left:23px;top:509px">Welcome to Brontex Solvents</h1>
  <p class="abs intro">The point of using Lorem Ipsum is that it has a more-or-less normal distribution of letters, as opposed to using 'Content here, content here', making it look like readable English. Many desktop publishing packages and web page editors now use Lorem Ipsum as their default model text, and a search for 'lorem ipsum' will uncover many web sites still in their infancy</p>

  <h2 class="abs h2" style="left:23px;top:621px">Our Other Deals<span class="arrows">‹ ›</span></h2>

  <div class="abs deal-img" style="left:32px;background:linear-gradient(90deg,#ddd 0%,#a33 30%,#c77a1a 55%,#e8e8e8 80%)" role="img" aria-label="Test tubes of lubricant"></div>
  <div class="abs deal-title" style="left:28px">Lubricants</div>
  <p class="abs deal-text" style="left:28px">Nor again is there anyone who loves or pursues or desires to obtain pain</p>
  <div class="abs readmore" style="left:27px">readmore</div>

  <div class="abs deal-img" style="left:239px;background:linear-gradient(135deg,#9a9a9a 0%,#cfcfcf 40%,#6a5a3a 70%,#444 100%)" role="img" aria-label="Motor oil being poured into an engine"></div>
  <div class="abs deal-title" style="left:232px">Motor oils</div>
  <p class="abs deal-text" style="left:232px">Nor again is there anyone who loves or pursues or desires to obtain pain</p>
  <div class="abs readmore" style="left:231px">readmore</div>

  <div class="abs deal-img" style="left:438px;background:linear-gradient(135deg,#b22 0%,#e9e4c8 40%,#555 70%,#2a2a2a 100%)" role="img" aria-label="Brake fluid reservoir in an engine bay"></div>
  <div class="abs deal-title" style="left:433px">Brake-fluids</div>
  <p class="abs deal-text" style="left:433px">Nor again is there anyone who loves or pursues or desires to obtain pain</p>
  <div class="abs readmore" style="left:432px">readmore</div>

  <h2 class="abs h2" style="left:23px;top:851px">Testimonials<span class="arrows">‹ ›</span></h2>
  <div class="abs avatar" style="top:889px" role="img" aria-label="Client photo placeholder"></div>
  <div class="abs quote-name" style="top:889px">mr. Daniel Marsh (California)</div>
  <p class="abs quote-text" style="top:904px">Many desktop publishing packages and web page editors now use Lorem Ipsum as their default model text,</p>
  <div class="abs link" style="left:82px;top:946px">read more</div>
  <div class="abs avatar" style="top:985px" role="img" aria-label="Client photo placeholder"></div>
  <div class="abs quote-name" style="top:984px">mr. Daniel Marsh (California)</div>
  <p class="abs quote-text" style="top:999px">Many desktop publishing packages and web page editors now use Lorem Ipsum as their default model text,</p>
  <div class="abs link" style="left:82px;top:1041px">read more</div>

  <h2 class="abs h2" style="left:397px;top:851px">LatesNews<span class="arrows">‹ ›</span></h2>
  <div class="abs news-title" style="top:884px">Brake-fluids</div>
  <p class="abs news-text" style="top:909px">Nor again is there anyone who loves or pursues or desires to obtain pain</p>
  <div class="abs link" style="left:398px;top:951px">read more</div>
  <div class="abs news-title" style="top:983px">Brake-fluids</div>
  <p class="abs news-text" style="top:1008px">Nor again is there anyone who loves or pursues or desires to obtain pain</p>
  <div class="abs link" style="left:398px;top:1050px">read more</div>
</main>

<aside>
  <div class="abs sidebar"></div>
  <h3 class="abs h2" style="left:627px;top:508px">Products Finder</h3>
  <div class="abs field" style="left:619px;top:532px;width:156px">Enter text</div>
  <div class="abs btn" style="left:781px;top:532px;width:50px">Search</div>

  <h3 class="abs h2" style="left:627px;top:569px">Products A-Z</h3>
  <div class="abs az-tab">
    <svg width="54" height="20" viewBox="0 0 54 20" aria-hidden="true"><path d="M12 13 L17 8 L22 13" stroke="#fff" stroke-width="2.5" fill="none"/><path d="M33 8 L38 13 L43 8" stroke="var(--gold)" stroke-width="2.5" fill="none"/></svg>
  </div>
  <div class="abs az-box">
    <p><b>Catalyst 512</b><br>Marlow Polymers</p>
    <p><b>Thermaflo™ and KW 3100B</b><br>Kestrel Wax (Industrial)</p>
    <p><b>Velora Foaming Agents</b><br>Velora Chemie</p>
    <p><b>Clorinex® and Purava® Sodium Chlorite</b><br>Hallstead Industries</p>
  </div>

  <h3 class="abs h2" style="left:627px;top:801px">Market Sectors</h3>
  <ul class="abs sectors">
    <li>Coatings, Inks and Adhesives</li>
    <li>Home Care, Industrial &amp; Institutional Products</li>
    <li>Haircare</li>
  </ul>

  <h3 class="abs h2" style="left:627px;top:920px">Our Location</h3>
  <div class="abs map" role="img" aria-label="Street map of Dubai showing the company location"></div>
</aside>

<footer>
  <div class="abs footer"></div>
  <div class="abs foot-links">Home | About Us | Partners | Business Fields | Products | Contact Us</div>
  <div class="abs copy">All © Copyrights.korvane.Reserved</div>
  <div class="abs newsletter">Newsletter</div>
  <div class="abs field" style="left:628px;top:1154px;width:155px;background:#ccc;padding-left:8px">Enter your e-Mail I.D here</div>
  <div class="abs btn" style="left:790px;top:1154px;width:48px">Search</div>
</footer>

</body>
</html>
```